Create modern and sleek business card for luxury real estate company

We're a "boutique" real estate office looking for a design that gets across a highly modern luxury brand. Blacks and whites are probably the best colors unless we try a silver foil for the logo. I've attached a version of our current logo here. I'd like to swap out the current font on there with Gotham Light Regular.

I'm looking to have one side of the card have the logo with the space for our agents info on the other side.

Target Market(s)

Young professionals in a "luxury" headspace

Industry/Entity Type

Real estate

Contact Information for Business Card

A place for agent name, cell number, website. The slogan "Simply Rethinking Real Estate".

Font styles to use
Other font styles liked:
• Gotham Regular

Colors

Designer to choose only greyscale colors for use in the design.

Requirements
Must have
• Matte black as the background color. Clean lines and use of contrast. A specific design aspect that will use silver foil.
Nice to have
• Up in the air on integrating a QR code
Should not have
• Any houses or other real estate related design (ex: a clip art house)

```html
<!DOCTYPE html>
<html lang="en">
<head>
<meta charset="utf-8">
<title>Alder Realty – Business Card</title>
<link href="https://fonts.googleapis.com/css2?family=Montserrat:wght@400;500&display=swap" rel="stylesheet">
<style>
  :root {
    --page-bg: #e6e4e1;
    --card-black: #1c1c1e;
    --card-edge: #3a3a3c;
    --silver: #d9d9d9;
    --silver-soft: #bdbdbd;
    --text-white: #f2f2f2;
  }
  html, body {
    margin: 0;
    padding: 0;
    width: 1200px;
    height: 887px;
    overflow: hidden;
    background: var(--page-bg);
  }
  .canvas {
    position: relative;
    width: 1200px;
    height: 887px;
  }
  .business-card {
    position: absolute;
    left: 100px;
    top: 171px;
    width: 1000px;
    height: 545px;
    border-radius: 26px;
    background: var(--card-black);
    box-shadow: 0 0 0 2px var(--card-edge), 0 18px 40px rgba(0,0,0,0.25);
    font-family: "Montserrat", sans-serif;
    color: var(--text-white);
    overflow: hidden;
  }
  .brand-lockup {
    position: absolute;
    left: 62px;
    top: 58px;
    display: flex;
    align-items: center;
    gap: 16px;
  }
  .brand-dot {
    width: 62px;
    height: 62px;
    border-radius: 50%;
    border: 2px solid var(--silver);
    box-sizing: border-box;
  }
  .brand-name {
    font-weight: 400;
    font-size: 30px;
    line-height: 1.15;
    letter-spacing: 2px;
    color: var(--silver);
  }
  .agent-name {
    position: absolute;
    left: 60px;
    top: 235px;
    margin: 0;
    font-weight: 500;
    font-size: 28px;
    letter-spacing: 1px;
    text-transform: uppercase;
  }
  .agent-title {
    position: absolute;
    left: 60px;
    top: 277px;
    margin: 0;
    font-weight: 400;
    font-size: 21px;
    color: var(--silver-soft);
  }
  .contact-list {
    position: absolute;
    left: 56px;
    top: 388px;
    margin: 0;
    padding: 0;
    list-style: none;
    font-size: 21px;
    letter-spacing: 0.5px;
  }
  .contact-item {
    display: flex;
    align-items: center;
    gap: 12px;
    height: 33px;
  }
  .contact-icon {
    width: 16px;
    height: 16px;
    fill: none;
    stroke: var(--text-white);
    stroke-width: 1.6;
  }
  .foil-seal {
    position: absolute;
    left: 498px;
    top: 46px;
    width: 440px;
    height: 440px;
  }
  .foil-seal-name {
    font-family: "Montserrat", sans-serif;
    font-weight: 400;
    font-size: 34px;
    letter-spacing: 4px;
    fill: var(--silver);
  }
</style>
</head>
<body>
<div class="canvas">
  <section class="business-card">
    <div class="brand-lockup">
      <div class="brand-dot"></div>
      <div class="brand-name">ALDER<br>REALTY</div>
    </div>

    <h1 class="agent-name">Daniel Harper</h1>
    <p class="agent-title">Director</p>

    <ul class="contact-list">
      <li class="contact-item">
        <svg class="contact-icon" viewBox="0 0 16 16"><path d="M4 1.5 L6 5 L4.5 6.5 C5.5 8.8 7.2 10.5 9.5 11.5 L11 10 L14.5 12 L13 14.5 C7 14 2 9 1.5 3 Z"/></svg>
        <span>555.014.2290</span>
      </li>
      <li class="contact-item">
        <svg class="contact-icon" viewBox="0 0 16 16"><rect x="1.5" y="3.5" width="13" height="9"/><path d="M1.5 3.5 L8 9 L14.5 3.5"/></svg>
        <span>info@alderhomes.com</span>
      </li>
      <li class="contact-item">
        <svg class="contact-icon" viewBox="0 0 16 16"><circle cx="8" cy="8" r="6.5"/><ellipse cx="8" cy="8" rx="3" ry="6.5"/><path d="M1.5 8 H14.5"/></svg>
        <span>www.alderhomes.com</span>
      </li>
    </ul>

    <svg class="foil-seal" viewBox="0 0 440 440">
      <circle cx="220" cy="220" r="214" fill="none" stroke="var(--silver)" stroke-width="5"/>
      <text class="foil-seal-name" x="220" y="232" text-anchor="middle">ALDER REALTY</text>
    </svg>
  </section>
</div>
</body>
</html>
```